Q + Public Adjusters Collective Business card

We need to get business card Design for our Company we are Public Adjusters in Chicago Illinois - i like to see good combination and elements from my Company Logo. as well To be an two side design
Updates

Target Market(s)

Home /Business owner Property Managers

Industry/Entity Type

Business

Contact Information for Business Card

to show the Element of our logo i will Like 3D

Font styles to use
Sans Serif

Requirements
Must have
• Logo and Element of the Logo in 3D
Nice to have
• Logo That we Provide 3D Same Colors or open for suggestions
Should not have
• unleare view -

```html
<!DOCTYPE html>
<html lang="en">
<head>
<meta charset="utf-8">
<title>Public Adjusters Collective – Business Card</title>
<link rel="stylesheet" href="https://fonts.googleapis.com/css2?family=Roboto:wght@400;500;700&display=swap">
<style>
  :root {
    --stage: #303030;
    --card-white: #ffffff;
    --brand-blue: #1a2ea6;
    --brand-blue-dark: #0c1a6e;
    --brand-orange: #e0583a;
    --text-grey: #555a60;
  }
  * { box-sizing: border-box; margin: 0; padding: 0; }
  html, body {
    width: 1105px; height: 1200px; overflow: hidden;
    background: var(--stage);
    font-family: "Roboto", Arial, sans-serif;
  }
  .canvas { position: relative; width: 1105px; height: 1200px; }
  .card {
    position: absolute; left: 192px; width: 720px; height: 411px; overflow: hidden;
  }
  .card--front { top: 167px; background: var(--card-white); }
  .card--back { top: 622px; background: var(--brand-orange); }

  .accent-tab {
    position: absolute; left: 0; top: 50px; width: 9px; height: 58px;
    background: linear-gradient(90deg, var(--brand-blue-dark), var(--brand-blue));
  }
  .holder-name {
    position: absolute; left: 41px; top: 52px;
    font-size: 26px; font-weight: 700; color: var(--brand-blue); letter-spacing: 0.3px;
  }
  .holder-title {
    position: absolute; left: 41px; top: 86px;
    font-size: 20px; font-weight: 400; color: var(--brand-orange);
  }
  .address {
    position: absolute; left: 41px; top: 172px;
    font-size: 18.5px; line-height: 26px; color: var(--text-grey);
  }
  .contact-list {
    position: absolute; left: 41px; top: 231px; list-style: none;
  }
  .contact-list li {
    display: flex; align-items: center; height: 27.5px;
    font-size: 18.5px; color: var(--text-grey);
  }
  .contact-list svg { width: 18px; height: 18px; margin-right: 9px; fill: var(--brand-blue); flex: none; }

  .footer-band { position: absolute; left: 0; bottom: 0; width: 720px; height: 19px; }

  .brand-mark {
    position: absolute; display: flex; flex-direction: column; align-items: center;
  }
  .brand-mark--front { left: 404px; top: 138px; width: 300px; }
  .brand-dot { border-radius: 50%; background: var(--brand-blue); }
  .brand-mark--front .brand-dot { width: 120px; height: 120px; margin-bottom: 40px; }
  .brand-name {
    font-size: 22px; font-weight: 700; color: var(--brand-blue); white-space: nowrap;
  }
  .brand-mark--back { left: 0; top: 70px; width: 720px; }
  .brand-mark--back .brand-dot { width: 170px; height: 170px; background: var(--card-white); margin-bottom: 18px; }
  .brand-mark--back .brand-name { color: var(--card-white); font-size: 24px; }
  .back-url {
    position: absolute; left: 0; top: 346px; width: 720px; text-align: center;
    font-size: 18px; letter-spacing: 2.4px; color: var(--card-white);
  }
</style>
</head>
<body>
<main class="canvas">
  <section class="card card--front" aria-label="Business card front">
    <div class="accent-tab"></div>
    <h1 class="holder-name">MARA KELLEN</h1>
    <p class="holder-title">President</p>
    <p class="address">2417 Larchmont Avenue<br>Evanston, IL 60201</p>
    <ul class="contact-list">
      <li><svg viewBox="0 0 20 20" aria-hidden="true"><path d="M2 6c0-2 3-4 8-4s8 2 8 4v2h-4V6.5C12.5 6 7.5 6 6 6.5V8H2z"/><rect x="4" y="9" width="12" height="9" rx="1"/></svg>312 4185 0927</li>
      <li><svg viewBox="0 0 20 20" aria-hidden="true"><path d="M6 1h8a1 1 0 0 1 1 1v16a1 1 0 0 1-1 1H6a1 1 0 0 1-1-1V2a1 1 0 0 1 1-1zm1 2v12h6V3z"/></svg>773 6021 4480</li>
      <li><svg viewBox="0 0 20 20" aria-hidden="true"><rect x="5" y="2" width="10" height="5"/><rect x="1" y="8" width="18" height="8" rx="1"/><rect x="5" y="13" width="10" height="5"/></svg>312 4185 0930</li>
      <li><svg viewBox="0 0 20 20" aria-hidden="true"><path d="M1 4h18v12H1z"/><path d="M2 5l8 6 8-6" fill="none" stroke="#fff" stroke-width="1.4"/></svg>mara@qpaclaims.com</li>
      <li><svg viewBox="0 0 20 20" aria-hidden="true"><circle cx="10" cy="10" r="8.5"/><path d="M6 6c2 1 3 0 4 2s-1 3 1 4 1 3 0 5" fill="none" stroke="#fff" stroke-width="1.5"/></svg>www.qpaclaims.com</li>
    </ul>
    <div class="brand-mark brand-mark--front">
      <div class="brand-dot"></div>
      <p class="brand-name">Public Adjusters Collective</p>
    </div>
    <svg class="footer-band" viewBox="0 0 720 19" preserveAspectRatio="none" aria-hidden="true">
      <defs>
        <linearGradient id="bandBlue" x1="0" x2="1">
          <stop offset="0" stop-color="#0c1a6e"/>
          <stop offset="0.55" stop-color="#2443d6"/>
          <stop offset="1" stop-color="#0c1a6e"/>
        </linearGradient>
      </defs>
      <polygon points="0,0 364,0 358,19 0,19" fill="url(#bandBlue)"/>
      <polygon points="373,0 720,0 720,19 367,19" fill="var(--brand-orange)"/>
    </svg>
  </section>

  <section class="card card--back" aria-label="Business card back">
    <div class="brand-mark brand-mark--back">
      <div class="brand-dot"></div>
      <p class="brand-name">Public Adjusters Collective</p>
    </div>
    <p class="back-url">www.PublicAdjustersCollective.com</p>
  </section>
</main>
</body>
</html>
```